Corvane Paintless Dent Removal

Our company works on vehicles removing dents using a highly skilled trade which the metal is massaged out with special tools without disturbing the original paint, hence paintless dent removal. Besides keeping the paint and metal original its also very environmentally friendly since no paint or toxic fillers are used. Also we we are one of the most experienced companies in the business with 25 years

Target Market(s)

Retail Automobile consumers, Auto Dealerships and Auto Body Shops

Industry/Entity Type

Auto Repair

Contact Information for Business Card

Dale Hollister
PO Box 518 Brookmere, NY 11962
631-555-0148
corvanepdr@mailbox-example.com
website corvanepdr.example
youtube corvane paintless dent removal
25 years of experience removing Dents, Dings and Hail Damage

Font styles to use
Serif
Sans Serif

Colors

Designer to choose colors to be used in the design.

Requirements
Must have
• I do like things that are simple but classy and somewhat bold, also I like my logo so that should be somewhat important

```html
<!DOCTYPE html>
<html lang="en">
<head>
<meta charset="utf-8">
<title>Corvane Paintless Dent Removal – Business Card</title>
<link rel="stylesheet" href="https://fonts.googleapis.com/css2?family=Roboto:wght@400;700;900&display=swap">
<style>
  :root {
    --backdrop: #2e2e2f;
    --card: #222223;
    --gloss: #6a6a6e;
    --green: #7dc21e;
    --blue: #0b4f9c;
    --ink: #f2f2f2;
  }
  html, body {
    margin: 0;
    padding: 0;
    width: 799px;
    height: 1200px;
    overflow: hidden;
    background: var(--backdrop);
    font-family: "Roboto", Arial, sans-serif;
  }
  .canvas {
    position: relative;
    width: 799px;
    height: 1200px;
  }
  .card {
    position: absolute;
    left: 80px;
    width: 640px;
    height: 366px;
    background: var(--card);
    border-radius: 3px;
    box-shadow: 0 10px 30px rgba(0,0,0,.45);
    overflow: hidden;
  }
  .card--front { top: 117px; }
  .card--back  { top: 717px; }

  .brand {
    position: absolute;
    inset: 0;
    display: flex;
    align-items: center;
    justify-content: center;
    gap: 14px;
  }
  .brand__dot {
    width: 18px;
    height: 18px;
    border-radius: 50%;
    background: var(--gloss);
    flex: none;
  }
  .brand__name {
    margin: 0;
    font-weight: 900;
    font-size: 32px;
    letter-spacing: .3px;
    color: var(--gloss);
  }

  .sweeps {
    position: absolute;
    inset: 0;
    width: 640px;
    height: 366px;
  }
  .sweep--blue  { fill: var(--blue); }
  .sweep--green { fill: var(--green); }

  .contact {
    position: absolute;
    inset: 0;
    display: flex;
    flex-direction: column;
    align-items: center;
    justify-content: center;
    text-align: center;
    color: var(--ink);
  }
  .contact__name {
    margin: 0;
    font-weight: 700;
    font-size: 30px;
    color: var(--green);
  }
  .contact__title {
    margin: 4px 0 12px;
    font-size: 15px;
  }
  .contact__rule {
    width: 300px;
    height: 1px;
    background: var(--green);
    border: 0;
    margin: 0 0 10px;
  }
  .contact__icons {
    display: flex;
    gap: 5px;
    margin-bottom: 10px;
  }
  .contact__icons svg { width: 13px; height: 13px; fill: var(--green); }
  .contact__line {
    margin: 2px 0;
    font-size: 15px;
    line-height: 1.3;
  }
</style>
</head>
<body>
<main class="canvas">

  <section class="card card--front" aria-label="Card front">
    <div class="brand">
      <span class="brand__dot" aria-hidden="true"></span>
      <h1 class="brand__name">Corvane Paintless Dent Removal</h1>
    </div>
  </section>

  <section class="card card--back" aria-label="Card back">
    <svg class="sweeps" viewBox="0 0 640 366" aria-hidden="true">
      <path class="sweep--blue" d="M0 0 H210 Q70 30 0 175 Z"/>
      <path class="sweep--blue" d="M0 205 Q40 90 170 40 Q90 100 0 230 Z" opacity=".9"/>
      <path class="sweep--green" d="M640 366 H430 Q570 336 640 191 Z"/>
      <path class="sweep--green" d="M640 161 Q600 276 470 326 Q550 266 640 136 Z" opacity=".9"/>
    </svg>
    <div class="contact">
      <h2 class="contact__name">Dale Hollister</h2>
      <p class="contact__title">Managing Director</p>
      <hr class="contact__rule">
      <div class="contact__icons" aria-hidden="true">
        <svg viewBox="0 0 16 16"><path d="M3 1h3l1.5 4-2 1.5a9 9 0 0 0 4 4L11 8.5l4 1.5v3c0 1-1 2-2 2C7 15 1 9 1 3c0-1 1-2 2-2z"/></svg>
        <svg viewBox="0 0 16 16"><path d="M1 3h14v10H1z M1 3l7 6 7-6" fill="none" stroke="#7dc21e" stroke-width="1.8"/></svg>
        <svg viewBox="0 0 16 16"><circle cx="8" cy="8" r="6.5" fill="none" stroke="#7dc21e" stroke-width="1.6"/><path d="M1.5 8h13M8 1.5c-3 3.5-3 9.5 0 13M8 1.5c3 3.5 3 9.5 0 13" fill="none" stroke="#7dc21e" stroke-width="1.3"/></svg>
      </div>
      <p class="contact__line">631-555-0148</p>
      <p class="contact__line">corvanepdr@mailbox-example.com | www.corvanepdr.example</p>
      <p class="contact__line">PO Box 518 Brookmere, NY 11962</p>
    </div>
  </section>

</main>
</body>
</html>
```